Letterhead and matching envelope design for a dental office

We need a new stationary design, letterhead and envelope #10, for a dental office in Denver area. We are called Bright Harbor Dental. We want a simple and minimalistic design but not a boring design. I wish to have one good point that makes it look professional. I have attached our logo. Feel free to use either one. I want the design for letterhead and envelope look like a "matching pair" but not look the same. The envelope doesn't have to be white and it will have an address window on bottom left.

Target Market(s)

everyone who visits dentist (adults)

Industry/Entity Type

Dental

Font styles to use
Other font styles liked:
• close to font on logo or something that matches well

Requirements
Must have
• professional
• simple, minimalistic
• unique point that stands out
Nice to have
• matching but not same design for letterhead and envelope
Should not have
• not look like all the other boring designs
• no flowery, distracting feats

```html
<!DOCTYPE html>
<html lang="en">
<head>
<meta charset="utf-8">
<title>Bright Harbor Dental – #10 Envelope</title>
<link href="https://fonts.googleapis.com/css2?family=Source+Sans+3:wght@400;600&display=swap" rel="stylesheet">
<style>
  :root {
    --backdrop: #ece9e4;
    --paper: #ffffff;
    --brand-green: #3cb54b;
    --band-light: #b3dfb6;
    --ink: #2b2b2b;
  }
  html, body {
    margin: 0;
    padding: 0;
    width: 1200px;
    height: 800px;
    overflow: hidden;
    background: var(--backdrop);
    font-family: "Source Sans 3", "Myriad Pro", Arial, sans-serif;
  }
  .canvas {
    position: relative;
    width: 1200px;
    height: 800px;
  }
  .envelope-flap {
    position: absolute;
    left: 218px;
    top: 158px;
    width: 764px;
    height: 136px;
  }
  .flap-brand {
    position: absolute;
    left: 500px;
    top: 208px;
    width: 200px;
    text-align: center;
    color: var(--paper);
    font-size: 13px;
    font-weight: 600;
    letter-spacing: 2px;
    line-height: 1.2;
    text-transform: uppercase;
  }
  .envelope-body {
    position: absolute;
    left: 218px;
    top: 292px;
    width: 764px;
    height: 333px;
    background: var(--paper);
    box-shadow: 0 2px 6px rgba(0,0,0,0.12);
  }
  .brand-mark {
    position: absolute;
    left: 34px;
    top: 30px;
    display: flex;
    align-items: center;
    gap: 8px;
    color: var(--brand-green);
    font-size: 17px;
    font-weight: 600;
    letter-spacing: 2px;
    text-transform: uppercase;
    line-height: 1.15;
  }
  .brand-mark .dot {
    width: 14px;
    height: 14px;
    border-radius: 50%;
    background: var(--brand-green);
    flex: none;
  }
  .return-address {
    position: absolute;
    left: 34px;
    top: 251px;
    font-size: 14.5px;
    line-height: 19px;
    color: var(--ink);
  }
  .return-address .practice-name {
    color: var(--brand-green);
  }
  .contact-list {
    position: absolute;
    left: 251px;
    top: 268px;
    margin: 0;
    padding: 0;
    list-style: none;
    font-size: 14.5px;
    line-height: 19px;
    color: var(--ink);
  }
  .contact-list li {
    display: flex;
    align-items: center;
    gap: 6px;
  }
  .contact-list svg {
    width: 15px;
    height: 15px;
    flex: none;
  }
  .band-light {
    position: absolute;
    top: 309px;
    height: 8px;
    background: var(--band-light);
  }
  .band-light.left { left: 0; width: 530px; }
  .band-light.right { right: 0; width: 44px; }
  .web-address {
    position: absolute;
    right: 46px;
    top: 303px;
    font-size: 14.5px;
    color: var(--brand-green);
  }
  .band-dark {
    position: absolute;
    left: 0;
    bottom: 0;
    width: 100%;
    height: 12px;
    background: var(--brand-green);
  }
</style>
</head>
<body>
<div class="canvas">
  <svg class="envelope-flap" viewBox="0 0 764 136" aria-hidden="true">
    <path d="M15 136 L15 84 Q15 74 40 70 L330 8 Q382 -4 434 8 L740 70 Q752 74 756 84 L764 136 Z" fill="var(--brand-green)"/>
  </svg>
  <div class="flap-brand">Bright Harbor<br>Dental</div>

  <div class="envelope-body">
    <div class="brand-mark">
      <span class="dot"></span>
      <span>Bright Harbor<br>Dental</span>
    </div>

    <div class="return-address">
      <div class="practice-name">Bright Harbor Dental</div>
      <div>2870 Lakeview Blvd,</div>
      <div>Suite 210 Arvada, CO 80004</div>
    </div>

    <ul class="contact-list">
      <li>
        <svg viewBox="0 0 16 16" aria-hidden="true">
          <circle cx="8" cy="8" r="8" fill="var(--brand-green)"/>
          <path d="M5.2 4.2l1.4-.3.8 2-1 .8a5 5 0 0 0 2.9 2.9l.8-1 2 .8-.3 1.4c-4 .3-6.9-2.6-6.6-6.6z" fill="#fff"/>
        </svg>
        720-555-0148
      </li>
      <li>
        <svg viewBox="0 0 16 16" aria-hidden="true">
          <circle cx="8" cy="8" r="8" fill="var(--brand-green)"/>
          <rect x="4" y="5" width="8" height="6" fill="#fff"/>
          <path d="M4 5l4 3.2L12 5" fill="none" stroke="var(--brand-green)" stroke-width="1"/>
        </svg>
        info@brightharbordental.com
      </li>
    </ul>

    <div class="band-light left"></div>
    <span class="web-address">www.brightharbordental.com</span>
    <div class="band-light right"></div>
    <div class="band-dark"></div>
  </div>
</div>
</body>
</html>
```